Wordpress Design Project

Hi,

I would like a more modern colourful design doing for my website ZAP Lnx (www.za%plnx.com - remove percentage). But I do still want to keep the same sort of colors, just maybe lighter. More interesting.

I want the inside pages to NOT all look the same with just boring text.

I want the site to look more appealing and maybe a new logo.
Updates

I would like to mention I would prefer to keep the same logo after rethinking it (possibly a slight refresh of the logo if you feel its a good idea) and the same color scheme as at present.

Saves us rebranding a lot of our apps, tools online ads etc.

Also I thought it is worth mentioning we have 2 parts to the site. The front end and the logged in area. It would be good if when making the front end you keep in mind the back end at http://p.za%plnx.com (remove percentage). We can only edit this limitedly (can edit the entire footer, the logo and full CSS of it). Would be good if we could make sure the header and footer can be used on the back end as well maybe to make it match.

I also want layouts making not just for the homepage. Obviously every page will basically be the same but I don't want all the other pages to just be 'text' and no real layout.

You can see out main pages on the website at the moment, I want those other pages to be laid out nice and differently as well. For example the testimonials page could be more interesting with speech bubbles and pictures of each person (just use placeholders). The affiliates page could be a description and then a nice fancy list of features why to join etc. 

Nothing overly complicated but I think it makes the whole site seem a lot better.

Target Market(s)

Affiliate Marketing. International.

Requirements
Must have
• Needs to be more room for links across the navigation at the top, also sub menus (at present we have a lot of pages which are hidden deep within other pages).
Nice to have
• Lists of features for advertisers and affiliates on the homepage part.

Menu items and buttons have nice hover over effects.

I want to get across on our pages all the different unique features we have.

Maybe some kind of slider which has past offer logos in, just use example logos.

```html
<!DOCTYPE html>
<html lang="en">
<head>
<meta charset="utf-8">
<title>ZAP Lnx – Affiliate Network</title>
<link href="https://fonts.googleapis.com/css2?family=PT+Sans:wght@400;700&family=Yanone+Kaffeesatz:wght@400;500&display=swap" rel="stylesheet">
<style>
:root{
  --orange:#f7861c;
  --orange-light:#fbae3c;
  --orange-dark:#e8661e;
  --header:#4b4b4b;
  --nav:#353535;
  --footer:#3f3f3f;
  --page:#f1f1f1;
  --blue-title:#215a8c;
  --text:#333;
  --white:#fff;
}
*{box-sizing:border-box;margin:0;padding:0}
html,body{width:1154px;height:1200px;overflow:hidden}
body{font-family:"PT Sans",sans-serif;color:var(--text);background:var(--page);position:relative}
.abs{position:absolute}
.site-header{position:absolute;left:0;top:0;width:1154px;height:122px;background:linear-gradient(#555,#444)}
.brand{position:absolute;left:133px;top:36px;display:flex;align-items:center;gap:10px}
.brand-mark{width:26px;height:26px;background:var(--white)}
.brand-name{font-family:"PT Sans",sans-serif;font-weight:400;font-size:36px;color:var(--white);line-height:1}
.brand-tag{position:absolute;left:133px;top:82px;font-size:12px;color:var(--white)}
.phone{position:absolute;left:758px;top:31px;display:flex;align-items:center;gap:6px;color:#fff;font-size:21px}
.header-link{position:absolute;left:793px;top:79px;color:#fff;font-size:12px}
.main-nav{position:absolute;left:0;top:122px;width:1154px;height:49px;background:var(--nav);border-bottom:1px solid #222}
.main-nav ul{list-style:none}
.main-nav li{position:absolute;top:16px;color:#fff;font-size:14px}
.main-nav .sep{position:absolute;top:14px;width:1px;height:21px;background:#888}
.hero{position:absolute;left:0;top:171px;width:1154px;height:340px;background:radial-gradient(ellipse at 75% 40%,var(--orange-light),var(--orange) 55%,var(--orange-dark))}
.hero-frame{position:absolute;left:127px;top:26px;width:479px;height:297px;background:#fff;border:1px solid #ddd;box-shadow:0 6px 8px rgba(0,0,0,.25);padding:3px}
.hero-img{width:100%;height:100%;background:radial-gradient(circle at 50% 40%,#cfe9f7,#f6fbfe 70%)}
.hero-title{position:absolute;left:632px;top:83px;font-family:"Yanone Kaffeesatz",sans-serif;font-weight:400;font-size:27px;color:#fff;letter-spacing:.3px}
.hero-text{position:absolute;left:632px;top:117px;width:356px;color:#fff;font-size:13px;line-height:17.3px;text-align:justify}
.btn-join{position:absolute;left:632px;top:204px;width:225px;height:49px;border-radius:8px;background:linear-gradient(#555,#111);color:#fff;font-family:"Yanone Kaffeesatz",sans-serif;font-size:21px;display:flex;align-items:center;justify-content:center;box-shadow:0 3px 4px rgba(0,0,0,.3)}
.dots{position:absolute;left:1068px;top:313px;display:flex;gap:3px}
.dots span{width:10px;height:10px;border-radius:50%;background:#f4e5c8}
.dots span.on{background:#f6c600}
.login-tab{position:absolute;left:128px;top:534px;width:208px;height:60px;border-radius:6px 6px 0 0;background:linear-gradient(var(--orange-light),var(--orange-dark));color:#fff;font-size:19px;padding:17px 0 0 17px}
.login-box{position:absolute;left:128px;top:588px;width:270px;height:204px;border-radius:0 6px 6px 6px;background:linear-gradient(var(--orange-light),var(--orange-dark) 60%);box-shadow:0 3px 5px rgba(0,0,0,.2)}
.field{position:absolute;left:24px;width:209px;height:32px;background:linear-gradient(#fff,#e9e9e9);border:1px solid #ddd;font-size:12px;color:#555;padding:8px 0 0 33px}
.forgot{position:absolute;left:140px;top:121px;color:#fff;font-size:12px}
.btn-blue{position:absolute;top:147px;width:93px;height:38px;background:linear-gradient(#2f8ee0,#145fb0);border:1px solid #fff;color:#fff;font-size:17px;display:flex;align-items:center;justify-content:center}
.or{position:absolute;left:125px;top:159px;color:#fff;font-size:12px}
.section-title{font-family:"Yanone Kaffeesatz",sans-serif;font-size:22px;color:var(--blue-title);font-weight:500}
.welcome{position:absolute;left:448px;top:532px;width:565px}
.welcome h1 span{color:#222}
.welcome p{font-size:12.3px;line-height:17.3px;margin-top:17px;text-align:justify}
.welcome h1+p{margin-top:14px}
.col{position:absolute;top:834px;width:242px}
.col h2{border-bottom:1px solid #ddd;padding-bottom:2px}
.col p{font-size:12.3px;line-height:17.3px;margin-top:8px;text-align:justify}
.btn-orange{position:absolute;height:40px;border-radius:4px;background:linear-gradient(var(--orange-light),var(--orange-dark));color:#fff;font-family:"Yanone Kaffeesatz",sans-serif;font-size:19px;display:flex;align-items:center;justify-content:center;box-shadow:2px 3px 3px rgba(0,0,0,.25)}
.post-img{position:absolute;left:710px;top:878px;width:120px;height:89px;border:1px solid #ccc;background:#fff;padding:3px}
.post-img div{width:100%;height:100%;background:linear-gradient(#eee,#c9c9c9)}
.post{position:absolute;left:844px;top:876px;width:197px}
.post h3{font-family:Arial,sans-serif;color:var(--orange);font-size:14px;font-weight:700}
.post .meta{font-family:Arial,sans-serif;font-size:11.5px;color:#222;padding-bottom:5px;border-bottom:1px solid #ccc;margin-top:2px}
.post .excerpt{font-family:Arial,sans-serif;font-size:11px;color:#555;line-height:15.5px;margin-top:7px}
.side-tab{position:absolute;left:0;width:34px;background:#3a3a3a;border-radius:0 5px 5px 0;color:#fff;font-size:12.5px}
.side-tab span{position:absolute;left:9px;writing-mode:vertical-rl;transform:rotate(180deg)}
.site-footer{position:absolute;left:0;top:1097px;width:1154px;height:103px;background:linear-gradient(#444,#3a3a3a)}
.social{position:absolute;top:36px;width:25px;height:25px;border-radius:2px}
.footer-links{position:absolute;right:118px;top:30px;color:#fff;font-size:11.5px}
.copyright{position:absolute;right:118px;top:56px;color:#ddd;font-size:11.5px}
.x2{position:absolute;right:120px;top:74px;color:#ddd;font-size:11px}
</style>
</head>
<body>
<header class="site-header">
  <div class="brand">
    <span class="brand-mark"></span>
    <span class="brand-name">ZAP Lnx</span>
  </div>
  <div class="brand-tag">Earn money &amp; increase sales</div>
  <div class="phone">
    <svg width="22" height="26" viewBox="0 0 22 26"><path d="M4 2l5 0 2 7-3 2c1 4 4 8 8 10l2-3 4 3-1 4c-2 1-5 1-8-1C7 20 3 13 2 7 2 5 3 3 4 2z" fill="#f7861c"/></svg>
    <span>+44 (0)1000 555019</span>
  </div>
  <div class="header-link">Privacy Policy &amp; Cookies</div>
</header>

<nav class="main-nav">
  <ul>
    <li style="left:145px">HOME</li>
    <li style="left:238px">ABOUT US</li>
    <li style="left:359px">OUR BLOG</li>
    <li style="left:478px">TESTIMONIALS</li>
    <li style="left:622px">AFFILIATES</li>
    <li style="left:744px">ADVERTISERS</li>
    <li style="left:880px">CONTACT US</li>
  </ul>
  <i class="sep" style="left:211px"></i><i class="sep" style="left:329px"></i><i class="sep" style="left:451px"></i><i class="sep" style="left:594px"></i><i class="sep" style="left:713px"></i><i class="sep" style="left:851px"></i>
</nav>

<section class="hero">
  <div class="hero-frame"><div class="hero-img" role="img" aria-label="Globe connected to people and laptops around it"></div></div>
  <h2 class="hero-title">INTERNATIONAL AFFILIATE NETWORK TODAY</h2>
  <p class="hero-text">Sed ut perspiciatis unde omnis iste natus error sit voluptatem accusantium doloremque laudantium, totam rem aperiam, eaque ipsa quae ab illo inventore veritatis et quasi architecto beatae vitae dicta sunt</p>
  <div class="btn-join">JOIN US TODAY</div>
  <div class="dots"><span></span><span></span><span class="on"></span></div>
</section>

<div class="login-tab">ACCOUNT LOGIN</div>
<form class="login-box">
  <div class="field" style="top:26px">Email</div>
  <div class="field" style="top:75px">Passwod</div>
  <div class="forgot">Forgot Password</div>
  <div class="btn-blue" style="left:21px">LOGIN</div>
  <div class="or">or</div>
  <div class="btn-blue" style="left:138px">SIGN UP</div>
</form>

<section class="welcome">
  <h1 class="section-title">WELCOME TO <span>ZAP LNX</span></h1>
  <p>Welcome to the ZAP Lnx affiliate network. On time payments, hot &amp; exclusive CPL/CPA offers, fast support and low fees for advertisers, is the making of a leading affiliate network!</p>
  <p>ZAP Lnx offer a wide range of advertisers for your websites. So you can start monetizing your traffic or get an additional revenue stream, today.</p>
  <p>With the ZAP Lnx Affiliate Network we focus on lead generation offers. We have a range of competitions, surveys, incentives and gambling offers. Whatever the industry, you will be able to find offers to suit your traffic.</p>
  <p>ZAP Lnx is a powerful performance-based internet marketing network dedicated to advertisers to affiliates through its powerful affiliate network.</p>
</section>

<section class="col" style="left:146px">
  <h2 class="section-title">AFFILIATES</h2>
  <p>Get access to a wide range of top performing offers for your websites and email marketing lists. Fresh and exclusive offers to promote. Join over 2,000 affiliates already signed up to ZAP Lnx.</p>
</section>
<div class="btn-orange" style="left:147px;top:971px;width:142px">SIGN UP NOW</div>

<section class="col" style="left:426px">
  <h2 class="section-title">ADVERTISERS</h2>
  <p>Generate sales/leads to your website instantly with the ZAP Lnx Affiliate Network. Only pay on performance, no monthly or setup fees. ZAP Lnx takes the risk out of advertising</p>
</section>
<div class="btn-orange" style="left:427px;top:971px;width:142px">SIGN UP NOW</div>

<section class="col" style="left:706px;width:335px">
  <h2 class="section-title">RECENT BLOG POSTS</h2>
</section>
<div class="post-img"><div role="img" aria-label="Group of business people standing together"></div></div>
<article class="post">
  <h3>Lorem ipsum dolor sit amet,</h3>
  <div class="meta">Posted by: Admin &nbsp;|&nbsp; MArch 30 2013</div>
  <p class="excerpt">incididunt ut labore et dolore magna enim ad minim veniam, quis nostrud exercitation ullamco laboris nisi ut</p>
</article>
<div class="btn-orange" style="left:950px;top:977px;width:75px;height:37px">MORE</div>

<div class="side-tab" style="top:633px;height:133px"><span style="top:8px">Cooking Control</span>
  <svg class="abs" style="left:7px;top:108px" width="20" height="20" viewBox="0 0 20 20"><circle cx="10" cy="10" r="8" fill="#fff"/><circle cx="10" cy="10" r="4" fill="#f7861c"/></svg>
</div>
<div class="side-tab" style="top:790px;height:120px"><span style="top:14px">Onlie Chat</span>
  <svg class="abs" style="left:7px;top:92px" width="20" height="16" viewBox="0 0 20 16"><path d="M2 2h13v8H7l-4 3v-3H2z" fill="#f7861c"/></svg>
</div>

<footer class="site-footer">
  <div class="social" style="left:148px;background:#3b5a98"></div>
  <div class="social" style="left:184px;background:#3bb3e6"></div>
  <div class="social" style="left:221px;background:#333;border:1px solid #777"></div>
  <div class="social" style="left:259px;background:#f09a1c"></div>
  <div class="social" style="left:295px;background:#c4201b"></div>
  <div class="social" style="left:333px;background:#7c98b4"></div>
  <div class="footer-links">Affiliate Terms &amp; Conditions &nbsp;|&nbsp; Advertiser Terms &amp; Conditions &nbsp;|&nbsp; Privacy Policy &amp; Cookies &nbsp;|&nbsp; FAQ &nbsp;|&nbsp; Contact Us</div>
  <div class="copyright">© 2013 zaplnx, All Rights Reserved</div>
  <div class="x2">x2</div>
</footer>
</body>
</html>
```